a business advisory consulting website

I need a website 3-5 pages to sell my professional services in IT and Project management Consulting. My company name is Crestline Advisory Consulting. I want it to be device friendly and easy to navigate for the busy executive however intriguing enough.
I have attached some info I drafted on About the company and personal Bio. Also there is a website that I really like that I have attached the initial site pdf and websites that I like are here: https://tollmeradvisors.example, https://quarvelanalytics.example, https://www.dorvikstudylearning.example as examples. Thanks
Updates

Hi Designers, I have uploaded the logo in 3D .png format, to assist in the web design.

Target Market(s)

B2B, governments, IT companies, Project Management companies and Consulting firms, small medium enterprises to large corporate enterprises.

Industry/Entity Type

It Professional

Coding

Coded - Design and coding required

Number of Pages Required

5+ page

Font styles to use
Sans Serif

Requirements
Must have
• Home, About company, the team, what we do and contact us
Nice to have
• Blog
Should not have
• pop ups, flash

```html
<!DOCTYPE html>
<html lang="en">
<head>
<meta charset="utf-8">
<title>Crestline Advisory Consulting</title>
<link rel="stylesheet" href="https://fonts.googleapis.com/css2?family=Poppins:wght@500;600;700&family=Roboto:wght@400;500;700&display=swap">
<style>
:root{
  --navy:#242a4a;
  --red:#e3262b;
  --ink:#2a2f45;
  --body:#5b5f6e;
  --soft:#f4f4f6;
  --white:#ffffff;
  --panel:rgba(92,98,118,.88);
}
*{margin:0;padding:0;box-sizing:border-box}
html,body{width:1200px;height:4087px;overflow:hidden}
body{position:relative;background:var(--white);font-family:'Roboto',Arial,sans-serif;color:var(--body);font-size:14px;line-height:25.7px}
.abs{position:absolute}
.heading{font-family:'Poppins',Arial,sans-serif;font-weight:600;color:var(--ink);line-height:1.1}
.accent{color:var(--red)}
.label{font-family:'Poppins',Arial,sans-serif;font-size:13px;letter-spacing:4px;color:#c9ccd4;font-weight:600;text-transform:uppercase}
.rule{height:2px;width:76px;background:var(--navy)}
.rule.light{background:var(--white)}
.btn{display:flex;align-items:center;justify-content:center;background:var(--red);color:var(--white);font-weight:700;font-size:13.5px;text-transform:uppercase;height:45px;width:135px}

.topline{left:0;top:0;width:1200px;height:3px;background:var(--red)}
.header{left:0;top:3px;width:1200px;height:103px;background:var(--white);border-bottom:1px solid #e6e6ea}
.brand{left:111px;top:36px;display:flex;align-items:center;gap:10px}
.brand-mark{width:26px;height:26px;background:var(--red)}
.brand-name{font-family:'Poppins',Arial,sans-serif;font-weight:700;font-size:21px;color:var(--navy);letter-spacing:.5px}
.nav{top:50px;font-size:14px;color:var(--ink)}
.nav.current{color:var(--red)}
.header-btn{left:954px;top:38px;width:133px}

.hero{left:0;top:107px;width:1200px;height:566px;background:linear-gradient(110deg,#e9e9ea 0%,#d5d4d3 45%,#8f8a86 70%,#b48560 100%)}
.hero-panel{left:0;top:262px;width:600px;height:254px;background:var(--panel);clip-path:polygon(0 0,100% 0,91% 100%,0 100%)}
.hero-edge{left:540px;top:262px;width:60px;height:254px;background:var(--red);clip-path:polygon(88% 0,100% 0,16% 100%,4% 100%)}
.hero-title{left:108px;top:296px;font-size:50px;color:var(--white);font-weight:600}
.hero-text{left:111px;top:366px;width:440px;color:var(--white);font-weight:700;font-size:13px;line-height:26px}
.dots{left:106px;top:623px;display:flex;gap:4px}
.dot{width:11px;height:11px;border-radius:50%;background:var(--white)}
.dot.on{background:var(--red)}

.about-photo{left:600px;top:620px;width:489px;height:602px;background:linear-gradient(160deg,#eef0f2,#c7cbd2 60%,#8a8d96)}

.why{left:0;top:1222px;width:1200px;height:459px;background:var(--navy)}
.why-photo{left:127px;top:1241px;width:370px;height:422px;background:linear-gradient(135deg,#b3837a,#6d4e55 60%,#3d3f5c)}

.portrait{left:654px;top:1776px;width:390px;height:390px;border-radius:50%;background:linear-gradient(150deg,#eceae8,#b9b1a9 60%,#5c5148)}
.portrait-ring{left:650px;top:1772px}

.health{left:0;top:2792px;width:1200px;height:588px;background:var(--navy)}
.on-dark .heading{color:var(--white)}

.contact{left:0;top:3380px;width:1200px;height:629px;background:var(--soft)}
.contact-line{left:183px;display:flex;gap:22px;align-items:flex-start;font-size:13.5px}
.contact-line svg{margin-top:7px;flex:none}
.social{top:3827px;width:27px;height:27px;border-radius:50%;background:var(--red)}
.field{left:632px;width:455px;height:56px;background:var(--white);padding:16px 26px;font-size:13.5px;color:#8a8d98;line-height:24px}
.send{left:632px;top:3895px;width:147px;height:58px}

.footer{left:0;top:4009px;width:1200px;height:78px;background:var(--navy);color:var(--white);font-size:13px;display:flex;align-items:center;justify-content:center;padding-right:42px}
</style>
</head>
<body>

<header>
  <div class="abs topline"></div>
  <div class="abs header"></div>
  <div class="abs brand"><span class="brand-mark"></span><span class="brand-name">CRESTLINE ADVISORY</span></div>
  <nav>
    <span class="abs nav current" style="left:442px">Home</span>
    <span class="abs nav" style="left:510px">About company</span>
    <span class="abs nav" style="left:641px">The team</span>
    <span class="abs nav" style="left:731px">What we do</span>
    <span class="abs nav" style="left:836px">Contact us</span>
  </nav>
  <div class="abs btn header-btn">Get Started</div>
</header>

<section>
  <div class="abs hero" role="img" aria-label="Smiling business man and woman standing in a bright office"></div>
  <div class="abs hero-panel"></div>
  <div class="abs hero-edge"></div>
  <h1 class="abs heading hero-title">Crestline Advisory</h1>
  <p class="abs hero-text">To get started straight away, simply tap any placeholder text<br>(such as this) and start typing.</p>
  <div class="abs btn" style="left:111px;top:436px">Get Started</div>
  <div class="abs dots"><span class="dot"></span><span class="dot on"></span><span class="dot"></span><span class="dot"></span></div>
</section>

<section>
  <div class="abs about-photo" role="img" aria-label="Consultant presenting at a flip chart during a meeting"></div>
  <div class="abs label" style="left:111px;top:768px">Who we are</div>
  <h2 class="abs heading" style="left:111px;top:790px;font-size:34px">About <span class="accent">Crestline Advisory</span></h2>
  <div class="abs rule" style="left:89px;top:845px"></div>
  <p class="abs" style="left:111px;top:860px;width:480px">We are a specialist operational excellence firm, delivering consulting and advisory services in six core capabilities, across all industries and all business lines to improve performance, efficiency, profitability, automation and scalability, for clients across Australia.<br>We’re known for our pragmatism, in depth analysis, strategic insight and nurturing long-term client self-sufficiency. We approach business consulting differently, with a Genuine Client Partnership model that builds client capability and rightsized solutions for the client.</p>
  <div class="abs btn" style="left:111px;top:1082px">Contact us</div>
</section>

<section class="on-dark">
  <div class="abs why"></div>
  <div class="abs why-photo" role="img" aria-label="Smiling businessman in a suit"></div>
  <h2 class="abs heading" style="left:592px;top:1308px;font-size:34px;font-weight:700">WHY WE EXIST</h2>
  <div class="abs rule light" style="left:570px;top:1361px"></div>
  <div class="abs" style="left:592px;top:1378px;width:490px;color:var(--white)">
    <p>Our aim at Halvern Capital is to be a leading strategy and financial advisory firm across the continent solving complex management problems for small and medium sized enterprises across a wide range of industries.</p>
    <p style="margin-top:25.7px">We help you scale your business operations to become highly profitable.</p>
    <p style="margin-top:25.7px">We offer your organization cutting-edge expertise leveraging on first-class, strategic and financial insights that help you simplify and structure your processes to become a lean efficient enterprise.</p>
  </div>
</section>

<section>
  <div class="abs label" style="left:111px;top:1773px">Our team</div>
  <h2 class="abs heading" style="left:111px;top:1795px;font-size:34px">Elias <span class="accent">Marrow</span></h2>
  <div class="abs rule" style="left:89px;top:1850px"></div>
  <div class="abs" style="left:111px;top:1866px;width:480px">
    <p>Elias Marrow is an IT professional with more than 20 years of experience turning business initiatives into technology solutions. His expertise has been identifying deficiencies and developing or facilitating the best solutions for an outcome that is satisfactory to all stakeholders involved.</p>
    <p style="margin-top:25.7px">Elias improves business processes as older organizations restructure or migrate to newer technologies. He bridges the gap between the actual people in these organizations transitioning and the new technologies they seek which is a value add to any organization’s success.</p>
  </div>
  <div class="abs btn" style="left:111px;top:2112px">Read more</div>
  <div class="abs portrait" role="img" aria-label="Portrait of the team lead in a dark suit"></div>
  <svg class="abs portrait-ring" width="398" height="398" viewBox="0 0 398 398">
    <path d="M300 40 A195 195 0 0 1 80 354" fill="none" stroke="#e3262b" stroke-width="6"/>
  </svg>
</section>

<section>
  <div class="abs" style="left:111px;top:2260px;width:443px;height:414px;border:1px solid #cfd2d8;background:linear-gradient(135deg,#e6e7e9,#b9b4ae 55%,#4a4c5a)" role="img" aria-label="Colleagues discussing documents around a meeting table"></div>
  <div class="abs label" style="left:603px;top:2269px">What we do</div>
  <h2 class="abs heading" style="left:603px;top:2293px;font-size:34px;font-weight:700;line-height:35px">PROCESS IMPROVEMENT<br>WITHIN GOVERNMENT</h2>
  <div class="abs rule" style="left:581px;top:2381px"></div>
  <p class="abs" style="left:603px;top:2396px;width:485px">Across the three levels of Government – Federal, State/Territory and Local – leaders continually face complex decisions around how to allocate limited resources to best service their citizens. In the past, Governments have faced criticism for an over reliance on bureaucracy and an inability to adapt or even prepare for the future. However, the trend among global leaders now is one of innovation both in how they run the business of Government and in the services they apply their resources to. Programs of innovation and transformation are actively sponsored to promote</p>
  <div class="abs btn" style="left:603px;top:2619px">Read more</div>
</section>

<section class="on-dark">
  <div class="abs health"></div>
  <div class="abs label" style="left:111px;top:2879px;color:#9ea3b8">What we do</div>
  <h2 class="abs heading" style="left:111px;top:2903px;font-size:34px;font-weight:700;line-height:35px">TECHNOLOGY ANALYSIS<br>WITHIN HEALTHCARE</h2>
  <div class="abs rule light" style="left:89px;top:2991px"></div>
  <p class="abs" style="left:111px;top:3006px;width:485px;color:var(--white)">Australia’s healthcare system is a complex web of public and private providers, settings, participants and supporting mechanisms. Health providers include medical practitioners, nurses, allied and other health professionals, hospitals, clinics and government agencies and private providers. These providers deliver a complete range of services across many levels, from public health and preventive services in the community, to primary health care, emergency health services, hospital-based treatment, and rehabilitation and palliative care.</p>
  <div class="abs btn" style="left:111px;top:3228px">Read more</div>
  <div class="abs" style="left:636px;top:2869px;width:443px;height:413px;background:linear-gradient(135deg,#d8dde3,#8d7b70 55%,#e7a25a)" role="img" aria-label="Doctor with stethoscope reviewing notes with a colleague"></div>
</section>

<section>
  <div class="abs contact"></div>
  <h2 class="abs heading" style="left:0;width:1200px;text-align:center;top:3466px;font-size:34px">Get In <span class="accent">Touch</span></h2>
  <div class="abs rule" style="left:562px;top:3518px"></div>
  <div class="abs contact-line" style="top:3545px;width:400px">
    <svg width="10" height="13" viewBox="0 0 10 13"><path d="M5 0a5 5 0 0 1 5 5c0 3-5 8-5 8S0 8 0 5a5 5 0 0 1 5-5z" fill="#e3262b"/><circle cx="5" cy="5" r="1.8" fill="#f4f4f6"/></svg>
    <span>Lorem ipsum dolor sit amet, consectetur adipiscing elit, sed do eiusmod tempor incididunt ut labore</span>
  </div>
  <div class="abs contact-line" style="top:3623px">
    <svg width="11" height="11" viewBox="0 0 11 11"><path d="M2 0l2 2.5-1.2 1.4a7 7 0 0 0 4.3 4.3L8.5 7 11 9l-1.5 2C4.5 11 0 6.5 0 1.5z" fill="#e3262b"/></svg>
    <span>+1 555 010 0199</span>
  </div>
  <div class="abs contact-line" style="top:3675px">
    <svg width="12" height="9" viewBox="0 0 12 9"><rect width="12" height="9" fill="#e3262b"/><path d="M0 0l6 5 6-5" fill="none" stroke="#f4f4f6" stroke-width="1.2"/></svg>
    <span>info@halverncapital.example</span>
  </div>
  <p class="abs" style="left:183px;top:3726px;width:400px;font-size:13.5px">Lorem ipsum dolor sit amet, consectetur adipiscing elit, sed do eiusmod tempor incididunt ut labore et dolore magna aliqua. Ut enim ad minim veniam, quis nostrud exercitation</p>
  <span class="abs social" style="left:182px"></span>
  <span class="abs social" style="left:227px"></span>
  <span class="abs social" style="left:271px"></span>
  <span class="abs social" style="left:316px"></span>
  <span class="abs social" style="left:360px"></span>
  <span class="abs social" style="left:404px"></span>

  <div class="abs field" style="top:3547px">Name</div>
  <div class="abs field" style="top:3617px">Email</div>
  <div class="abs field" style="top:3687px">Phone</div>
  <div class="abs field" style="top:3757px;height:125px">Message</div>
  <div class="abs btn send">Send</div>
</section>

<footer class="abs footer">© Copyrights 2020 Company name | All Rights Reserved</footer>

</body>
</html>
```